Business Card Design Project

We are a construction company in Orange County, CA. We need a two sided business card. We would like the back to be our logo with web URL. Front should included Name, title, address, phone, fax and email address.

our address is
627 West Dorrance Blvd, Suite 308
Anaheim, CA 92718

Our logo files are attached.

Construction

```html
<!DOCTYPE html>
<html lang="en">
<head>
<meta charset="utf-8">
<title>Kestra Business Card</title>
<link href="https://fonts.googleapis.com/css2?family=Source+Sans+3:wght@400;600;700&display=swap" rel="stylesheet">
<style>
  :root {
    --brand-blue: #124a7c;
    --paper: #ffffff;
    --rule-grey: #a9adb2;
    --ink-grey: #333333;
    --backdrop: #e4e6e8;
  }
  * { margin: 0; padding: 0; box-sizing: border-box; }
  html, body {
    width: 960px; height: 1200px; overflow: hidden;
    background: var(--backdrop);
    font-family: "Source Sans 3", "Myriad Pro", Arial, sans-serif;
  }
  .canvas { position: relative; width: 960px; height: 1200px; }

  .card {
    position: absolute;
    border-radius: 28px;
    overflow: hidden;
  }
  .card-front { left: 60px; top: 106px; width: 840px; height: 479px; background: var(--paper); }
  .card-back  { left: 55px; top: 645px; width: 840px; height: 477px; background: var(--brand-blue); }

  .wordmark {
    position: absolute; left: 0; width: 100%;
    text-align: center; font-weight: 700; line-height: 1;
  }
  .card-front .wordmark { top: 83px; font-size: 136px; letter-spacing: 4px; color: var(--brand-blue); }
  .card-back .wordmark  { top: 149px; font-size: 184px; letter-spacing: 6px; color: var(--paper); }

  .rule { position: absolute; left: 0; width: 100%; height: 3px; background: var(--rule-grey); }
  .rule-top { top: 290px; }
  .rule-bottom { top: 405px; }
  .contact-band {
    position: absolute; left: 0; top: 296px; width: 100%; height: 106px;
    background: var(--brand-blue); color: var(--paper);
  }
  .person { position: absolute; left: 32px; top: 20px; }
  .person-name { font-size: 35px; font-weight: 600; line-height: 1.1; }
  .person-title { font-size: 22px; font-weight: 700; line-height: 1.25; letter-spacing: 0.4px; }
  .contact-lines {
    position: absolute; right: 40px; top: 32px;
    text-align: right; font-size: 20px; line-height: 30px;
  }
  .contact-lines b { font-style: italic; font-weight: 700; }
  .sep { margin: 0 6px; }
  .address {
    position: absolute; left: 0; top: 434px; width: 100%;
    text-align: center; font-size: 21px; color: var(--ink-grey);
  }
  .web-url {
    position: absolute; left: 0; top: 400px; width: 100%;
    text-align: center; font-size: 31px; font-weight: 700; color: var(--paper);
  }
</style>
</head>
<body>
<main class="canvas">
  <section class="card card-front">
    <div class="wordmark">KESTRA</div>
    <div class="rule rule-top"></div>
    <div class="contact-band">
      <div class="person">
        <div class="person-name">Your Name</div>
        <div class="person-title">Designation</div>
      </div>
      <div class="contact-lines">
        <div><b>p</b> : 1-234-4567<span class="sep">|</span><b>f</b> : 1-234-4567</div>
        <div><b>e</b> : info@kestrabuild.com<span class="sep">|</span><b>w</b> : www.kestrabuild.com</div>
      </div>
    </div>
    <div class="rule rule-bottom"></div>
    <div class="address">627 West Dorrance Blvd, Suite 308, Anaheim, CA 92718</div>
  </section>

  <section class="card card-back">
    <div class="wordmark">KESTRA</div>
    <div class="web-url">www.kestrabuild.com</div>
  </section>
</main>
</body>
</html>
```